Home Remodeling company needs a business card design

we need a business card design for home remodeling company in hamilton county, indiana USA. we offers a wide range of construction services including whole house renovations, Design and Build Basements and Kitchen and Bathroom Remodeling . we would like to see designs for both site of business card that use the same color of the company logo and also including all information below :
1- Karim Feltous CEO / General Contractor
2- all company contacts Telephone numbers ( 1-888-DULOM-47 ) ( 317-555-0193) email address ( info@dulomhome.com) website ( www.dulomhome.com ) and social media logos (Facebook- twitter- google plus )
3- company logo
4- licensed . insured . bonded

```html
<!DOCTYPE html>
<html lang="en">
<head>
<meta charset="utf-8">
<title>DULOM Home Remodeling – Business Card</title>
<link href="https://fonts.googleapis.com/css2?family=Roboto:wght@400;700&display=swap" rel="stylesheet">
<style>
  :root {
    --backdrop: #3a302c;
    --card-dark: #2e2e2f;
    --card-light: #f1f1f1;
    --ink: #2b2b2c;
    --ink-soft: #444446;
    --accent: #c4303a;
    --band-dark: #333335;
    --paper-text: #ededed;
  }
  * { box-sizing: border-box; margin: 0; padding: 0; }
  html, body { width: 1200px; height: 716px; overflow: hidden; }
  body {
    background: var(--backdrop);
    font-family: "Roboto", Arial, sans-serif;
    position: relative;
  }
  .card {
    position: absolute;
    top: 210px;
    width: 520px;
    height: 297px;
    border-radius: 3px;
    overflow: hidden;
  }
  .card-back { left: 60px; background: var(--card-dark); }
  .card-front { left: 620px; background: var(--card-light); }

  .brand {
    font-family: "Roboto", Arial, sans-serif;
    font-weight: 700;
    line-height: 1;
    text-transform: uppercase;
  }
  .brand .brand-name { display: block; }
  .brand .brand-line { display: block; letter-spacing: 0.32em; }

  .card-back .brand {
    position: absolute; left: 50%; top: 50%;
    transform: translate(-50%, -50%);
    color: var(--paper-text);
  }
  .card-back .brand-name { font-size: 62px; letter-spacing: 0.02em; }
  .card-back .brand-line { font-size: 15px; margin-top: 6px; }

  .social { position: absolute; left: 34px; top: 30px; display: flex; gap: 4px; }
  .social span { width: 17px; height: 17px; background: var(--ink); border-radius: 2px; }

  .person { position: absolute; left: 40px; top: 98px; color: var(--ink); }
  .person-name { font-size: 21px; font-weight: 700; letter-spacing: 0.01em; }
  .person-title { font-size: 13px; margin-top: 4px; color: var(--ink-soft); }

  .card-front .brand {
    position: absolute; left: 262px; top: 72px;
    color: var(--ink);
  }
  .card-front .brand-name { font-size: 46px; letter-spacing: 0.02em; }
  .card-front .brand-line { font-size: 11px; margin-top: 4px; }

  .contacts {
    position: absolute; left: 290px; top: 144px;
    list-style: none; color: var(--ink); font-size: 15px;
  }
  .contacts li { display: flex; align-items: center; gap: 10px; height: 19px; }
  .contacts svg { width: 12px; height: 12px; fill: var(--accent); flex: none; }

  .bands { position: absolute; left: 0; bottom: 0; width: 520px; height: 66px; }
  .credentials {
    position: absolute; right: 28px; bottom: 16px;
    color: var(--paper-text); font-size: 15px; letter-spacing: 0.02em;
  }
</style>
</head>
<body>

  <section class="card card-back" aria-label="Card back">
    <div class="brand">
      <span class="brand-name">DULOM</span>
      <span class="brand-line">Home Remodeling</span>
    </div>
  </section>

  <section class="card card-front" aria-label="Card front">
    <div class="social" aria-label="Social media">
      <span></span><span></span><span></span>
    </div>

    <div class="person">
      <p class="person-name">Karim Feltous</p>
      <p class="person-title">CEO / General Contractor</p>
    </div>

    <div class="brand">
      <span class="brand-name">DULOM</span>
      <span class="brand-line">Home Remodeling</span>
    </div>

    <ul class="contacts">
      <li><svg viewBox="0 0 12 12"><path d="M2.5 0.8 L4.6 3 3.6 4.3 Q4.6 6.6 7.7 8.4 L9 7.4 11.2 9.5 9.8 11.2 Q5.5 11 2.4 7.6 Q0.6 5 0.8 2.2 Z"/></svg>1-888-DULOM-47</li>
      <li><svg viewBox="0 0 12 12"><path d="M1 4 Q6 0.5 11 4 L10 5.8 8 5 8 4 Q6 3.3 4 4 L4 5 2 5.8 Z M2.5 7 H9.5 V11 H2.5 Z"/></svg>317-555-0193</li>
      <li><svg viewBox="0 0 12 12"><path d="M0.5 2.5 H11.5 V9.5 H0.5 Z M1.2 3.2 L6 6.6 10.8 3.2 Z" fill-rule="evenodd"/></svg>info@dulomhome.com</li>
      <li><svg viewBox="0 0 12 12"><circle cx="6" cy="6" r="5.3"/><path d="M0.7 6 H11.3 M6 0.7 V11.3 M2 3 H10 M2 9 H10" stroke="#f1f1f1" stroke-width="0.8" fill="none"/></svg>www.dulomhome.com</li>
    </ul>

    <svg class="bands" viewBox="0 0 520 66" aria-hidden="true">
      <polygon points="0,4 235,4 225,20 0,20" fill="var(--accent)"/>
      <polygon points="252,4 520,4 520,66 218,66" fill="var(--band-dark)"/>
    </svg>
    <p class="credentials">Licensed &nbsp;•&nbsp; Insured &nbsp;•&nbsp; Bonded</p>
  </section>

</body>
</html>
```